RTavenor Business Cards & Letterhead

I have a logo but need a design for some new business cards. We are a Design-Build Firm that specializes in the design and construction of commercial projects.
the cards need to be professional. no cartoon stuff.
i would like to have the cards in AI format so I can update the card as needed. Logo is provided.
Our Address is: 4187 Marlowe Ct. Apex, North Carolina 27614

```html
<!DOCTYPE html>
<html lang="en">
<head>
<meta charset="utf-8">
<title>RTavenor Business Card</title>
<link rel="stylesheet" href="https://fonts.googleapis.com/css2?family=Open+Sans:wght@400;600;700;800&display=swap">
<style>
  :root {
    --stage: #333333;
    --card-white: #ffffff;
    --blue-light: #1b78bd;
    --blue-mid: #145f9a;
    --blue-deep: #0b3a62;
    --blue-back-center: #1673b4;
    --ink: #1a1a1a;
    --rule: #2a2a2a;
  }
  * { box-sizing: border-box; margin: 0; padding: 0; }
  html, body {
    width: 1200px; height: 780px; overflow: hidden;
    background: var(--stage);
    font-family: "Open Sans", Arial, sans-serif;
  }
  .stage {
    width: 1200px; height: 780px;
    display: flex; align-items: center; justify-content: center; gap: 40px;
  }
  .card {
    width: 520px; height: 297px; position: relative; overflow: hidden;
  }
  .card-back {
    background: radial-gradient(ellipse at 50% 55%, var(--blue-back-center) 0%, #13578f 45%, var(--blue-deep) 100%);
    display: flex; align-items: center; justify-content: center;
  }
  .back-wordmark {
    font-weight: 800; font-size: 50px; letter-spacing: 2px;
    color: #0e4675; text-transform: uppercase;
  }
  .card-front {
    background: var(--card-white);
    display: flex;
  }
  .brand-zone {
    width: 292px; display: flex; align-items: center; justify-content: center; gap: 10px;
  }
  .brand-square {
    width: 26px; height: 26px; background: var(--blue-mid); border-radius: 4px;
  }
  .brand-name {
    font-weight: 700; font-size: 28px; color: var(--blue-mid); letter-spacing: 1px;
  }
  .divider {
    width: 1px; background: var(--rule); margin: 52px 0 44px;
  }
  .contact-zone {
    flex: 1; padding: 58px 0 0 22px; color: var(--ink);
  }
  .person-name {
    font-weight: 800; font-size: 21px; line-height: 1; letter-spacing: 0.5px; text-transform: uppercase;
  }
  .person-name .first { color: var(--blue-light); }
  .person-name .last { color: var(--blue-deep); }
  .person-title { font-weight: 700; font-size: 13.5px; margin-top: 3px; }
  .address { font-size: 13px; line-height: 1.3; margin-top: 12px; }
  .contact-list { list-style: none; margin-top: 12px; font-size: 13px; line-height: 1.45; }
  .contact-list li { display: flex; align-items: center; gap: 8px; }
  .contact-list svg { width: 13px; height: 13px; flex: none; }
</style>
</head>
<body>
<main class="stage">
  <section class="card card-back" aria-label="Business card back">
    <span class="back-wordmark">RTavenor</span>
  </section>

  <section class="card card-front" aria-label="Business card front">
    <div class="brand-zone">
      <span class="brand-square"></span>
      <span class="brand-name">RTAVENOR</span>
    </div>
    <div class="divider"></div>
    <div class="contact-zone">
      <h1 class="person-name"><span class="first">Roland</span> <span class="last">Tavenor</span></h1>
      <p class="person-title">Founder/President</p>
      <p class="address">4187 Marlowe Ct. Apex,<br>North Carolina 27614</p>
      <ul class="contact-list">
        <li>
          <svg viewBox="0 0 16 16" aria-hidden="true"><path fill="#145f9a" d="M3.6 1.5l2.3 2.6-1.3 1.6c.9 1.9 2.4 3.4 4.3 4.3l1.6-1.3 2.6 2.3-1.4 2.2C6.8 13 3 9.2 1.4 4.3z"/></svg>
          (919) 555-0148
        </li>
        <li>
          <svg viewBox="0 0 16 16" aria-hidden="true"><circle cx="8" cy="8" r="7" fill="#145f9a"/><path fill="none" stroke="#fff" stroke-width="1" d="M1 8h14M8 1c-3 3-3 11 0 14M8 1c3 3 3 11 0 14"/></svg>
          www.rtavenor.com
        </li>
        <li>
          <svg viewBox="0 0 16 16" aria-hidden="true"><rect x="1" y="4" width="14" height="10" rx="1" fill="#145f9a"/><path fill="none" stroke="#fff" stroke-width="1.2" d="M1.5 4.5L8 10l6.5-5.5"/></svg>
          RST@RTavenor.com
        </li>
      </ul>
    </div>
  </section>
</main>
</body>
</html>
```